Letterhead and Envelope Only (no biz card)
Leadership Development & Coaching Start Up
I also really like it when the swirls are not perfectly positioned on the page...bleeding off the page looks good. Thanks everyone!
Thanks for submitting your designs! Something else to keep in mind, I am rather feminine...I prefer softer lines and fainter watermarks in the background. I also really prefer the contact info to be on the bottom of the design.
Correction, I like the contact info on the bottom in #1 (not #3.)
My logo designer is out of the country, I should have those files for you in the next couple of days.
From the three designs so far, I like the swirls in #2. I like the contact info on the bottom in #3.
If possible, I'd like to have 2 letterhead designs in my winner...so I can use both for various purposes.
could you please upload the ai or eps file of logo?

```html
<!DOCTYPE html>
<html lang="en">
<head>
<meta charset="utf-8">
<title>Velmora — Letterhead and Envelope</title>
<link href="https://fonts.googleapis.com/css2?family=Arimo:wght@400;700&display=swap" rel="stylesheet">
<style>
  :root {
    --brand-blue: #0f3d80;
    --brand-gold: #f6b21b;
    --paper: #ffffff;
    --paper-edge: #d9d9d9;
    --swirl-tint: rgba(246, 226, 160, 0.16);
    --ink: #333333;
    --backdrop: #ffffff;
  }
  html, body {
    margin: 0;
    width: 1200px;
    height: 1101px;
    overflow: hidden;
    background: var(--backdrop);
    font-family: "Arimo", Arial, sans-serif;
  }
  .stage { position: relative; width: 1200px; height: 1101px; }

  /* Letterhead */
  .letterhead {
    position: absolute; left: 45px; top: 36px; width: 726px; height: 1035px;
    background: var(--paper); border: 1px solid var(--paper-edge);
    overflow: hidden; box-sizing: border-box;
  }
  .letterhead__band { position: absolute; left: 0; top: 0; width: 100%; height: 18px; background: var(--brand-blue); }
  .letterhead__watermark {
    position: absolute; border-radius: 50%;
    background: radial-gradient(circle, var(--swirl-tint) 0%, rgba(246,226,160,0) 72%);
  }
  .letterhead__watermark--upper { left: 60px; top: 200px; width: 300px; height: 300px; }
  .letterhead__watermark--lower { left: 40px; top: 560px; width: 340px; height: 340px; }
  .letterhead__corner { position: absolute; right: 0; bottom: 0; }
  .letterhead__brand { position: absolute; left: 39px; top: 900px; }
  .letterhead__contact {
    position: absolute; left: 45px; top: 980px; margin: 0;
    font-size: 11px; line-height: 22px; color: var(--ink);
  }

  /* Wordmark */
  .wordmark { display: flex; align-items: center; gap: 10px; }
  .wordmark__name { font-weight: 700; font-size: 40px; color: var(--brand-blue); letter-spacing: -0.5px; line-height: 1; }
  .wordmark__dot { width: 22px; height: 22px; border-radius: 50%; background: var(--brand-gold); }
  .wordmark__tag { margin: 3px 0 0 2px; font-size: 8px; color: var(--brand-gold); letter-spacing: .5px; }

  /* Envelope */
  .envelope { position: absolute; left: 372px; top: 392px; width: 798px; height: 500px; }
  .envelope__body { position: absolute; inset: 0; }
  .envelope__watermark {
    position: absolute; left: 520px; top: 250px; width: 240px; height: 240px; border-radius: 50%;
    background: radial-gradient(circle, var(--swirl-tint) 0%, rgba(246,226,160,0) 72%);
  }
  .envelope__brand { position: absolute; left: 27px; top: 388px; }
  .envelope__address { position: absolute; left: 39px; top: 460px; margin: 0; font-size: 11px; color: var(--ink); }
</style>
</head>
<body>
<main class="stage">

  <section class="letterhead" aria-label="Letterhead">
    <div class="letterhead__band"></div>
    <div class="letterhead__watermark letterhead__watermark--upper" role="img" aria-label="Faint swirl watermark"></div>
    <div class="letterhead__watermark letterhead__watermark--lower" role="img" aria-label="Faint swirl watermark"></div>
    <svg class="letterhead__corner" width="186" height="118" viewBox="0 0 186 118">
      <path d="M0 118 C30 50 100 8 186 0 L186 118 Z" fill="var(--brand-gold)"/>
    </svg>
    <div class="letterhead__brand">
      <div class="wordmark"><span class="wordmark__name">velmora</span><span class="wordmark__dot"></span></div>
      <p class="wordmark__tag">leadership coaching</p>
    </div>
    <p class="letterhead__contact">
      4820 Larkfield Lane Tessford, CO 80412<br>
      P: 303-555-0148 &nbsp; E: mkestovic@thealderwickgroup.com &nbsp; www.velmoragroup.com
    </p>
  </section>

  <section class="envelope" aria-label="Envelope">
    <svg class="envelope__body" width="798" height="500" viewBox="0 0 798 500">
      <rect x="0.5" y="88" width="797" height="411.5" fill="var(--paper)" stroke="var(--paper-edge)"/>
      <path d="M0 88 L370 10 Q393 4 416 10 L798 88 L798 222 Q400 232 0 222 Z" fill="var(--brand-blue)"/>
      <path d="M663 500 C695 430 740 392 798 379 L798 500 Z" fill="var(--brand-gold)"/>
      <circle cx="393" cy="66" r="9" fill="var(--brand-gold)"/>
    </svg>
    <div class="envelope__watermark" role="img" aria-label="Faint swirl watermark"></div>
    <div class="envelope__brand">
      <div class="wordmark"><span class="wordmark__name">velmora</span><span class="wordmark__dot"></span></div>
      <p class="wordmark__tag">leadership coaching</p>
    </div>
    <p class="envelope__address">4820 Larkfield Lane Tessford, CO 80412</p>
  </section>

</main>
</body>
</html>
```